Redo our website for our Robotics company

We sell robotic equipment to the restaurant industry. Our current robot, is a cooking robot that cooks up to 15 lbs of food. We will provide a prior website as well as brand guidelines. We plan on using wordpress and take advantage of wordpress's visual (no code) editor.

Current website - https://kelvatrix88.com/ (please note we are only selling Tammo now and no longer selling Plavo+

We want someone to take our existing content and design the website as well as layout our content we provide. Here's a suggested site layout:

✅ KelvaTrix88 Website Wireframe / Site Map
1. Home

Purpose: Introduce Tammo, establish credibility, drive demo requests.

Sections:

Hero Section

Headline: “Meet Tammo — Your New Robotic Chef for High-Volume, Consistent Cooking.”

Sub-headline: Increase throughput. Reduce labor. Deliver perfect food every time.

CTA: Request a Demo + Watch Tammo Cook

Visual: Video loop or hero animation of Tammo in action.

How Tammo Works (3-4 steps)

Step cards: Load Ingredients → Select Recipe → Tammo Cooks → Serve

Icons and short explanations.

Key Benefits

Labor savings

Zero inconsistency

24/7 uptime

Throughput increases (30–50% faster)

Health & safety compliance

Who It’s For

QSR restaurants

Fast casual

Catering/commissaries

Ghost kitchens

Case Studies / Testimonials

Logo bar + quotes

“Tammo helped us reduce cooking times by 40%.”

Video Section

“Watch Tammo cook a full batch from start to finish.”

CTA Section

Big banner: Book a Demo

2. Product: “Meet Tammo”

Purpose: Deep dive into hardware, software, safety, reliability.

Sections:

Overview

What Tammo is

What tasks it automates

Where it fits in a kitchen

Hardware Features

High-temperature cooking chamber

Precision sensors

Automated stirring

Automated dispensing

Safety mechanisms (locking lids, auto-shutoff)

Software & AI

Recipe automation

IoT dashboard

Remote monitoring

Predictive maintenance

Specs Table

Dimensions

Power requirements

Capacity (lbs per batch)

Safety certifications

Gallery

Close-ups, installation photos, process shots

CTA: Request a Demo

3. Solutions

Purpose: Show that Tammo solves real operational problems.

Sub-pages or sections:

For Quick-Service Restaurants

Reduce labor cost

Speed up peak-hour demand

For Catering & Commissaries

Large-batch consistency

Automate repetitive cooking tasks

For High-Growth Chains

Replicable quality across multiple locations

Centralized recipe control

Each solution page includes:

A problem statement

How Tammo solves it

Metrics / KPIs

Relevant testimonial

CTA

4. ROI / Economics

Purpose: Sell the financial story clearly.

Sections:

Savings Calculator

Labor hours saved

Cost savings

Throughput increases

Food waste reduction

Before & After Comparison

Traditional kitchen vs. robotic kitchen

Sample ROI

“Payback in as little as 3–6 months.”

Download Full ROI Report (PDF)

5. Case Studies

Purpose: Social proof + real results.

Structure for each case study:

Customer background

Problem

Implementation

KPIs achieved

Labor savings

Consistency improvements

Cooking speed

Quote + photos/video

6. Pricing

Purpose: Start a commercial conversation.

Include:

Subscription model (monthly / annual)

Hardware leasing or purchase options

Installation + training

Support level

CTA to book a sales call

7. About

Purpose: Build trust.

Sections:

Mission statement

Founding team

Advisors/partners

“Why we built Tammo”

8. Resources

Purpose: SEO + education.

Subpages:

Blog (e.g., “The Future of Automated Kitchens”)

Whitepapers

Technical documentation

Product videos

9. Contact

General inquiry form

Sales contact

Support portal

Careers

```html
<!DOCTYPE html>
<html lang="en">
<head>
<meta charset="utf-8">
<title>KelvaTrix88 — Meet Tammo</title>
<link href="https://fonts.googleapis.com/css2?family=Montserrat:ital,wght@0,400;0,500;0,600;0,700;0,800;1,400&display=swap" rel="stylesheet">
<style>
:root{
  --orange:#f0532b;
  --orange-light:#ff7a3d;
  --navy:#0b2c5e;
  --blue-band:#4170a6;
  --ink:#1d1d1d;
  --muted:#555;
  --white:#fff;
  --black:#0a0a0a;
  --gold:#f4a51c;
}
*{box-sizing:border-box;margin:0;padding:0}
html,body{width:1200px;height:4127px;overflow:hidden;background:var(--white)}
body{position:relative;font-family:'Montserrat',sans-serif;color:var(--ink)}
.abs{position:absolute}
.accent{color:var(--orange)}
.btn{position:absolute;display:flex;align-items:center;justify-content:center;border-radius:22px;font-weight:700;font-size:13px;text-transform:uppercase}
.btn-orange{background:linear-gradient(90deg,var(--orange),var(--orange-light));color:var(--white)}
.btn-white{background:var(--white);color:var(--orange)}

/* hero */
.hero{left:8px;top:13px;width:1183px;height:653px;border-radius:10px;overflow:hidden;background:linear-gradient(180deg,#3b3d40 0%,#2a2b2d 55%,#4a4b4d 100%)}
.hero-shade{position:absolute;inset:0;background:rgba(0,0,0,.35)}
.logo-tab{left:505px;top:0;width:200px;height:68px;background:var(--white);clip-path:polygon(0 0,100% 0,88% 100%,12% 100%)}
.logo{font-weight:800;color:var(--orange);letter-spacing:-.5px}
.nav{font-size:14px;color:var(--white);font-weight:500}
.nav-home{left:100px;top:34px;width:63px;height:24px;border-radius:12px;background:var(--white);color:var(--orange);font-weight:700;font-size:13px;display:flex;align-items:center;justify-content:center}
.hero h1{position:absolute;left:0;width:1200px;top:205px;text-align:center;color:var(--white);font-size:52px;line-height:62px;font-weight:700}
.hero-sub{left:0;width:1200px;top:411px;text-align:center;color:var(--white);font-weight:700;font-size:20px}

/* headings */
.sec-title{position:absolute;left:0;width:1200px;text-align:center;font-size:44px;font-weight:400}
.sec-title b{font-weight:700}
.underline{position:absolute;height:4px;background:var(--orange)}

/* steps */
.step{position:absolute;width:220px;text-align:center}
.step-icon{width:112px;height:112px;margin:0 auto;border-radius:50%;border:2px dashed var(--navy);display:flex;align-items:center;justify-content:center}
.step-icon span{width:90px;height:90px;border-radius:50%;background:var(--navy);display:flex;align-items:center;justify-content:center}
.step.active .step-icon{border-color:var(--orange)}
.step.active .step-icon span{background:linear-gradient(180deg,var(--orange-light),var(--orange))}
.step h3{font-size:19px;font-weight:500;margin-top:14px}
.step.active h3{color:var(--orange);font-weight:700}
.step p{font-size:13px;line-height:25px;color:var(--muted);margin-top:8px}

/* audience */
.audience{left:0;top:1213px;width:1200px;height:608px;background:var(--blue-band)}
.card{position:absolute;top:1349px;width:311px;height:388px;background:var(--white);border-radius:4px}
.card .ph{position:absolute;left:9px;top:9px;width:293px;height:320px}
.card h3{position:absolute;bottom:20px;width:100%;text-align:center;font-size:21px;font-weight:500}

/* benefits */
.benefit{position:absolute;left:111px;display:flex;align-items:center;gap:16px;font-size:21px;font-weight:500}
.benefit i{width:58px;height:58px;border-radius:50%;background:var(--navy);display:flex;align-items:center;justify-content:center;flex:none}
.benefit.active{color:var(--orange);font-weight:700}
.benefit.active i{background:linear-gradient(180deg,var(--orange-light),var(--orange))}

/* footer */
.footer{left:8px;top:3738px;width:1183px;height:380px;background:var(--black);border-radius:6px}
.f-head{color:var(--white);font-weight:700;font-size:14px}
.f-list{color:var(--white);font-size:12.5px;line-height:25.6px;list-style:none}
.f-contact{color:var(--white);font-size:13px;display:flex;align-items:center;gap:18px}
</style>
</head>
<body>

<!-- HERO -->
<section class="abs hero">
  <div role="img" aria-label="Photo of Tammo cooking robots lined up in a commercial kitchen" style="position:absolute;inset:0;background:radial-gradient(ellipse at 50% 30%,#6a6c6f 0%,#2f3133 70%)"></div>
  <div class="hero-shade"></div>
  <div class="abs logo-tab"></div>
  <div class="abs logo" style="left:505px;top:18px;width:200px;text-align:center;font-size:26px">KelvaTrix88</div>
  <div class="abs nav-home">Home</div>
  <div class="abs nav" style="left:175px;top:37px">Product</div>
  <div class="abs nav" style="left:259px;top:37px">Solution</div>
  <div class="abs nav" style="left:334px;top:37px">Case Stusies</div>
  <div class="abs nav" style="left:715px;top:42px">ROI</div>
  <div class="abs nav" style="left:758px;top:42px">Pricing</div>
  <div class="abs nav" style="left:827px;top:42px">About</div>
  <div class="abs nav" style="left:888px;top:42px">Resources</div>
  <div class="btn btn-orange" style="left:982px;top:21px;width:115px;height:40px">Contact Us</div>
  <h1>Meet Tammo — Your New<br><span class="accent">Robotic Chef</span> for High-Volume,<br>Consistent Cooking.</h1>
  <div class="abs hero-sub">Increase throughput. Reduce labor. Deliver perfect food every time.</div>
  <div class="btn btn-orange" style="left:402px;top:453px;width:175px;height:39px">Request a Demo</div>
  <div class="btn btn-white" style="left:586px;top:453px;width:217px;height:39px;gap:6px">
    <svg width="16" height="16" viewBox="0 0 16 16"><circle cx="8" cy="8" r="8" fill="#f0532b"/><path d="M6 4.5v7l5.5-3.5z" fill="#fff"/></svg>Watch Tammo Cook</div>
</section>

<!-- HOW IT WORKS -->
<h2 class="sec-title" style="top:758px">How <b class="accent">Tammo Works</b></h2>
<div class="underline" style="left:558px;top:822px;width:84px"></div>

<div class="step" style="left:116px;top:881px">
  <div class="step-icon"><span><svg width="44" height="44" viewBox="0 0 44 44" fill="none" stroke="#fff" stroke-width="2.5"><path d="M6 22h32a16 12 0 0 1-32 0z"/><circle cx="16" cy="14" r="3"/><circle cx="26" cy="12" r="3"/><circle cx="21" cy="18" r="2"/></svg></span></div>
  <h3>Load Ingredients</h3>
  <p>Load up to 15 lbs of food into Tammo's high-capacity hopper.</p>
</div>
<div class="step" style="left:368px;top:881px">
  <div class="step-icon"><span><svg width="44" height="44" viewBox="0 0 44 44" fill="none" stroke="#fff" stroke-width="2.5"><rect x="6" y="6" width="12" height="12"/><rect x="24" y="6" width="12" height="12"/><rect x="6" y="24" width="12" height="12"/><path d="M27 38v-10l6 4"/></svg></span></div>
  <h3 style="margin-top:20px">Select Recipe</h3>
  <p>Choose preset recipes or customize based on your workflow.</p>
</div>
<div class="step active" style="left:617px;top:881px">
  <div class="step-icon"><span><svg width="44" height="44" viewBox="0 0 44 44" fill="none" stroke="#fff" stroke-width="2.5"><rect x="8" y="16" width="28" height="20" rx="2"/><path d="M14 16v-4h16v4M16 8c0-2 2-2 2-4M22 8c0-2 2-2 2-4M28 8c0-2 2-2 2-4"/></svg></span></div>
  <h3>Tammo Cooks</h3>
  <p>Precision robotic movement + automated temperature control.</p>
</div>
<div class="step" style="left:870px;top:881px">
  <div class="step-icon"><span><svg width="44" height="44" viewBox="0 0 44 44" fill="none" stroke="#fff" stroke-width="2.5"><path d="M8 30a14 14 0 0 1 28 0zM4 30h36M22 16v-4"/><path d="M6 36h32"/></svg></span></div>
  <h3>Serve</h3>
  <p>Tammo alerts your staff when food is ready for serving or holding.</p>
</div>

<!-- WHO IT'S FOR -->
<section class="abs audience"></section>
<h2 class="sec-title" style="top:1253px;color:var(--white)">Who <b>It’s For</b></h2>
<div class="card" style="left:112px"><div class="ph" role="img" aria-label="Photo of a modern quick-service restaurant dining room" style="background:linear-gradient(180deg,#6b5a48,#2e2822)"></div><h3>QSR Restaurants</h3></div>
<div class="card" style="left:444px"><div class="ph" role="img" aria-label="Photo of customers ordering at a fast casual counter" style="background:linear-gradient(180deg,#3c4a40,#1f5a48)"></div><h3>Fast casual</h3></div>
<div class="card" style="left:777px"><div class="ph" role="img" aria-label="Photo of a catering buffet with trays of food" style="background:linear-gradient(180deg,#8a6a4c,#2a2a2a)"></div><h3>Catering</h3></div>

<!-- BENEFITS -->
<h2 class="abs" style="left:116px;top:1893px;font-size:44px;font-weight:400">Key <b class="accent">Benefits</b></h2>
<div class="underline" style="left:112px;top:1956px;width:83px"></div>
<div class="benefit" style="top:1989px"><i><svg width="28" height="28" viewBox="0 0 28 28" fill="none" stroke="#fff" stroke-width="2"><circle cx="14" cy="9" r="5"/><path d="M5 26c0-6 4-9 9-9s9 3 9 9"/></svg></i>Labor savings</div>
<div class="benefit" style="top:2058px"><i><span style="color:#fff;font-weight:800;font-size:30px">0</span></i>Zero inconsistency</div>
<div class="benefit active" style="top:2126px"><i><svg width="30" height="30" viewBox="0 0 30 30" fill="none" stroke="#fff" stroke-width="2"><path d="M5 15a10 10 0 1 0 3-7M5 4v5h5M15 9v6l4 3"/></svg></i>24/7 uptime</div>
<div class="benefit" style="top:2195px"><i><svg width="28" height="28" viewBox="0 0 28 28" fill="#fff"><path d="M16 3L7 16h6l-2 9 9-13h-6z"/></svg></i>Throughput increases (30–50% faster)</div>
<div class="benefit" style="top:2264px"><i><svg width="28" height="28" viewBox="0 0 28 28"><path d="M14 3l9 4v7c0 6-4 10-9 12-5-2-9-6-9-12V7z" fill="#fff"/><path d="M10 14l3 3 5-6" stroke="#0b2c5e" stroke-width="2.2" fill="none"/></svg></i>Health &amp; safety compliance</div>
<div class="abs" role="img" aria-label="Photo of the Tammo cooking robot with its display screen" style="left:777px;top:1912px;width:316px;height:398px;border-radius:4px;background:linear-gradient(180deg,#2f3236,#8a8d90 60%,#555 100%)"></div>

<!-- VIDEO -->
<div class="abs" role="img" aria-label="Video still of Tammo cooking a batch of food" style="left:111px;top:2422px;width:494px;height:381px;border-radius:4px 0 0 4px;background:linear-gradient(135deg,#3a3c3f,#a5a8ab 55%,#4a4c4f)"></div>
<svg class="abs" style="left:343px;top:2600px" width="56" height="56" viewBox="0 0 56 56"><circle cx="28" cy="28" r="27" fill="#f0532b" stroke="#fff" stroke-width="2"/><circle cx="28" cy="28" r="16" fill="#fff"/><path d="M24 20v16l12-8z" fill="#f0532b"/></svg>
<div class="abs" style="left:605px;top:2422px;width:485px;height:381px;background:var(--navy);border-radius:0 4px 4px 0"></div>
<div class="abs" style="left:640px;top:2514px;color:var(--white);font-size:42px;line-height:62px;font-weight:500">Watch Tammo cook<br>a full batch from<br>start to finish.</div>

<!-- TESTIMONIALS -->
<h2 class="sec-title" style="top:2892px">Client <b class="accent">Testimonials</b></h2>
<div class="underline" style="left:558px;top:2956px;width:84px"></div>
<svg class="abs" style="left:39px;top:3039px" width="20" height="20"><circle cx="10" cy="10" r="10" fill="#f0532b"/><path d="M12 5l-5 5 5 5" stroke="#fff" stroke-width="2" fill="none"/></svg>
<svg class="abs" style="left:1136px;top:3039px" width="20" height="20"><circle cx="10" cy="10" r="10" fill="#999"/><path d="M8 5l5 5-5 5" stroke="#fff" stroke-width="2" fill="none"/></svg>
<div class="abs" style="left:411px;top:3027px;font-size:21px;font-weight:500">Kitchen Chef</div>
<div class="abs" style="left:563px;top:2999px;width:74px;height:74px;border-radius:50%;border:2px solid var(--orange)"></div>
<div class="abs" style="left:657px;top:3026px;color:var(--gold);font-size:22px;letter-spacing:1px">★★★★★</div>
<p class="abs" style="left:0;width:1200px;top:3084px;text-align:center;font-style:italic;font-size:27px;color:#555">Tammo helped us reduce cooking times by 40%.</p>

<!-- CTA -->
<div class="abs" style="left:112px;top:3211px;width:492px;height:420px;background:linear-gradient(160deg,var(--orange-light),var(--orange))"></div>
<div class="abs" role="img" aria-label="Photo of a smiling chef using a tablet beside a Tammo robot" style="left:604px;top:3211px;width:484px;height:420px;background:linear-gradient(135deg,#5a4a3e,#9a8a7a 50%,#3a3a3a)"></div>
<h2 class="abs" style="left:144px;top:3255px;color:var(--white);font-size:41px;line-height:56px;font-weight:700">Ready to See Tammo<br>Transform Your<br>Kitchen?</h2>
<p class="abs" style="left:149px;top:3441px;color:var(--white);font-size:17px;line-height:32px">Boost throughput, reduce labor stress, and<br>deliver consistent quality—every single time.</p>
<div class="btn btn-white" style="left:151px;top:3530px;width:149px;height:40px">Book a Demo</div>

<!-- FOOTER -->
<footer class="abs footer"></footer>
<div class="abs logo" style="left:117px;top:3812px;font-size:50px">KelvaTrix88</div>
<div class="abs" style="left:112px;top:3914px;width:316px;height:38px;border-radius:19px;background:var(--white);color:#888;font-size:12px;padding:12px 18px">Enter email address....</div>
<div class="btn btn-orange" style="left:112px;top:3975px;width:124px;height:39px">Subscribe</div>
<div class="abs f-head" style="left:539px;top:3806px">QUICK LINKS</div>
<ul class="abs f-list" style="left:542px;top:3833px"><li>Home</li><li>Product</li><li>Solution</li><li>Case Stusies</li><li>ROI</li><li>Pricing</li><li>About</li><li>Resources</li></ul>
<div class="abs f-head" style="left:685px;top:3806px">OTHERLINKS</div>
<ul class="abs f-list" style="left:688px;top:3833px"><li>Privacy policy</li><li>Termsd &amp; Conditions</li><li>Faq</li><li>Disclaimer</li><li>Help</li></ul>
<div class="abs f-head" style="left:873px;top:3806px">CONTACT INFO</div>
<div class="abs f-contact" style="left:875px;top:3847px"><svg width="22" height="22" viewBox="0 0 22 22"><path d="M11 1a7 7 0 0 0-7 7c0 5 7 13 7 13s7-8 7-13a7 7 0 0 0-7-7z" fill="#fff"/><circle cx="11" cy="8" r="2.5" fill="#000"/></svg>Lorem Ipsum,USA -437916</div>
<div class="abs f-contact" style="left:875px;top:3907px"><svg width="22" height="22" viewBox="0 0 22 22"><circle cx="11" cy="11" r="11" fill="#fff"/><path d="M7 6l2 0 1 3-1.5 1a7 7 0 0 0 3.5 3.5l1-1.5 3 1v2c-5 1-10-4-9-9z" fill="#000"/></svg>info@kelvatrix88.com</div>
<div class="abs f-contact" style="left:875px;top:3967px"><svg width="22" height="22" viewBox="0 0 22 22"><circle cx="11" cy="11" r="11" fill="#fff"/><rect x="5" y="7" width="12" height="8" fill="#000"/><path d="M5 7l6 5 6-5" stroke="#fff" fill="none"/></svg>+1 (555) 014 2288</div>
<svg class="abs" style="left:992px;top:4039px" width="96" height="28" aria-label="Social links"><circle cx="14" cy="14" r="13" fill="#f0532b"/><circle cx="46" cy="14" r="13" fill="#fff"/><circle cx="80" cy="14" r="13" fill="#fff"/></svg>
<div class="abs" style="left:112px;top:4076px;width:976px;height:1px;background:#444"></div>
<div class="abs" style="left:0;width:1200px;top:4090px;text-align:center;color:var(--white);font-size:13px;letter-spacing:.5px">KelvaTrix88 © 2025. All Rights Reserved.</div>

</body>
</html>
```